Coffeeshop menu for filter tip

We want to have a cannabis (coffeeshop) menu in the size 25mm wide x 60mm wide. Some examples attached.

it must have the following text:
Menu

WEED p/g
Oblivane €16
Cloudplum €14
Tide Runner €14
Quincefig €16
Mega Marsh €14
Grey Heron €14

HASH p/g
Tashar Amber €12
Pebble Frost€11
Lime Dunes €14
Ash Petal €10

Target Market(s)

tourist in Amsterdam

Requirements
Nice to have
• cannabis sign leaf
• No Cigarettes allowed symbol

```html
<!DOCTYPE html>
<html lang="en">
<head>
<meta charset="utf-8">
<title>Coffeeshop Menu</title>
<link rel="stylesheet" href="https://fonts.googleapis.com/css2?family=Jost:wght@300;400&display=swap">
<style>
  :root {
    --ink-black: #050505;
    --bg-dark: #111111;
    --bg-mid: #1b1b1b;
    --panel-weed: #1c1c1c;
    --panel-hash: #080808;
    --yellow: #f6f03a;
    --white: #ffffff;
    --grey: #9a9a9a;
    --skyline: #0e0e0e;
  }
  html, body {
    margin: 0;
    padding: 0;
    width: 1200px;
    height: 2880px;
    overflow: hidden;
    background: var(--ink-black);
  }
  .menu-card {
    display: block;
    width: 1200px;
    height: 2880px;
    font-family: "Jost", sans-serif;
  }
  .notice { fill: var(--white); font-size: 38px; font-weight: 400; letter-spacing: 0.22em; }
  .section-title { fill: var(--yellow); font-size: 125px; font-weight: 300; }
  .unit { fill: var(--grey); font-size: 60px; font-weight: 300; }
  .item-name { fill: var(--yellow); font-size: 78px; font-weight: 400; letter-spacing: 0.22em; }
  .price { fill: var(--white); font-size: 90px; font-weight: 300; letter-spacing: -0.04em; }
  .menu-title { fill: var(--white); font-size: 150px; font-weight: 300; }
  .icon-line { fill: none; stroke: var(--white); stroke-width: 4; }
</style>
</head>
<body>
<svg class="menu-card" viewBox="0 0 1200 2880" xmlns="http://www.w3.org/2000/svg">
  <defs>
    <radialGradient id="leafGlow" cx="0.5" cy="0.5" r="0.6">
      <stop offset="0" stop-color="#242424"/>
      <stop offset="1" stop-color="#0d0d0d"/>
    </radialGradient>
    <linearGradient id="skylineFade" x1="0" y1="0" x2="0" y2="1">
      <stop offset="0" stop-color="#1a1a1a"/>
      <stop offset="1" stop-color="#060606"/>
    </linearGradient>
  </defs>

  <!-- background -->
  <rect class="backdrop" x="0" y="0" width="1200" height="2880" fill="var(--bg-dark)"/>
  <rect class="leaf-pattern" role="img" aria-label="Faint cannabis leaf decoration" x="0" y="0" width="1200" height="2480" fill="url(#leafGlow)"/>

  <!-- no cigarettes notice -->
  <text class="notice" x="348" y="98">NO CIGARETTES</text>
  <g class="no-smoking-icon" transform="translate(826,85)">
    <circle class="icon-line" r="20"/>
    <rect x="-12" y="-3" width="24" height="8" fill="none" stroke="var(--white)" stroke-width="3"/>
    <line class="icon-line" x1="-14" y1="-14" x2="14" y2="14"/>
  </g>

  <!-- weed section -->
  <polygon class="weed-panel" points="208,373 944,373 1008,248 1200,248 1200,1456 208,1456" fill="var(--panel-weed)"/>
  <text class="section-title" x="264" y="340" textLength="656" lengthAdjust="spacing">WEED</text>
  <text class="unit" x="1152" y="375" text-anchor="end">p/g</text>

  <g class="weed-list">
    <text class="item-name" x="277" y="541">OBLIVANE</text>
    <text class="price" x="1149" y="541" text-anchor="end">€16</text>
    <text class="item-name" x="277" y="704">CLOUDPLUM</text>
    <text class="price" x="1149" y="704" text-anchor="end">€14</text>
    <text class="item-name" x="277" y="869" textLength="680" lengthAdjust="spacing">TIDE RUNNER</text>
    <text class="price" x="1149" y="869" text-anchor="end">€14</text>
    <text class="item-name" x="277" y="1034">QUINCEFIG</text>
    <text class="price" x="1149" y="1034" text-anchor="end">€16</text>
    <text class="item-name" x="277" y="1198">MEGA MARSH</text>
    <text class="price" x="1149" y="1198" text-anchor="end">€14</text>
    <text class="item-name" x="277" y="1363">GREY HERON</text>
    <text class="price" x="1149" y="1363" text-anchor="end">€14</text>
  </g>

  <!-- hash section -->
  <polygon class="hash-panel" points="0,1608 136,1608 256,1731 987,1731 987,2475 0,2475" fill="var(--panel-hash)"/>
  <text class="section-title" x="300" y="1696" textLength="628" lengthAdjust="spacing">HASH</text>
  <text class="unit" x="53" y="1736">p/g</text>

  <g class="hash-list">
    <text class="price" x="160" y="1896" text-anchor="end">€12</text>
    <text class="item-name" x="229" y="1896" textLength="690" lengthAdjust="spacing">TASHAR AMBER</text>
    <text class="price" x="160" y="2061" text-anchor="end">€11</text>
    <text class="item-name" x="229" y="2061" textLength="710" lengthAdjust="spacing">PEBBLE FROST</text>
    <text class="price" x="160" y="2224" text-anchor="end">€14</text>
    <text class="item-name" x="229" y="2224">LIME DUNES</text>
    <text class="price" x="160" y="2389" text-anchor="end">€10</text>
    <text class="item-name" x="229" y="2389">ASH PETAL</text>
  </g>

  <!-- city skyline strip -->
  <rect class="skyline" role="img" aria-label="Amsterdam city skyline silhouette" x="0" y="2475" width="1200" height="181" fill="url(#skylineFade)"/>

  <!-- footer -->
  <rect class="footer-band" x="0" y="2656" width="1200" height="224" fill="var(--ink-black)"/>
  <text class="menu-title" x="248" y="2811" textLength="704" lengthAdjust="spacing">MENU</text>
</svg>
</body>
</html>
```